PlumVesta screens tidy up

We would like advice on how to better present the following home page and overview pages.

The existing website is functional, but the pages don't appear professionals and pleasing to the eye. We would specifically like feedback on alignment and padding of icons and text to make the screen more appealing and polished.

We are following the quartzline design system.

1 page

Sans Serif
• IBM Plex, Poppins

```html
<!DOCTYPE html>
<html lang="en">
<head>
<meta charset="utf-8">
<title>PlumVesta – Home and Campaign Overview</title>
<link href="https://fonts.googleapis.com/css2?family=Inter:wght@400;500;600;700&display=swap" rel="stylesheet">
<style>
:root{
  --page:#dcdcdc;
  --white:#ffffff;
  --content:#f3f3f7;
  --sidebar:#404040;
  --ink:#1c1c1c;
  --muted:#4a4a4a;
  --soft:#6b6b6b;
  --track:#e4e4e8;
  --orange-a:#f0822a;
  --orange-b:#f8b84e;
  --navy:#1f3550;
  --bell:#e2403a;
  --online:#2fa84f;
}
*{box-sizing:border-box;margin:0;padding:0}
html,body{width:863px;height:1200px;overflow:hidden}
body{background:var(--page);font-family:"Inter",Arial,sans-serif;color:var(--ink);position:relative}
.screen{position:absolute;left:58px;width:747px;height:518px;background:var(--content);overflow:hidden}
.screen--home{top:45px}
.screen--overview{top:614px}
.brand{position:absolute;left:0;top:0;width:122px;height:33px;background:var(--white);display:flex;align-items:center;padding-left:15px;gap:6px}
.brand__mark{width:12px;height:12px;border-radius:50%;background:var(--orange-a)}
.brand__name{font-size:13px;font-weight:600;color:#444;letter-spacing:-.2px}
.topbar{position:absolute;left:122px;top:0;right:0;height:33px;background:var(--white)}
.topbar__title{position:absolute;left:13px;top:9px;font-size:10.5px;font-weight:600}
.topbar__icon{position:absolute;top:10px;width:13px;height:13px}
.avatar{position:absolute;left:591px;top:5px;width:23px;height:23px;border-radius:50%;background:linear-gradient(160deg,#c9d6ea,#5b73b4)}
.avatar__dot{position:absolute;right:-1px;top:-1px;width:6px;height:6px;border-radius:50%;background:var(--online);border:1px solid var(--white)}
.sidebar{position:absolute;left:0;top:33px;width:122px;height:485px;background:var(--sidebar)}
.nav{position:absolute;left:0;width:122px;height:16px;margin-top:-8px;display:flex;align-items:center;color:var(--white);font-size:8.5px;font-weight:500}
.nav__icon{position:absolute;left:10px;width:11px;height:11px}
.nav__label{position:absolute;left:28px}
.nav--group .nav__label{left:10px}
.nav__aside{position:absolute;right:9px;font-size:11px;font-weight:700}
.nav__chev{position:absolute;right:10px;width:6px;height:6px}
.nav--active{height:26px;margin-top:-13px;background:linear-gradient(90deg,var(--orange-a),var(--orange-b))}
.section-title{position:absolute;top:54px;font-size:9.5px;font-weight:600}
.card{position:absolute;background:var(--white);border-radius:4px;box-shadow:0 1px 3px rgba(0,0,0,.04)}
.hex{position:absolute;left:50%;width:44px;height:48px;margin-left:-22px}
.card__title{position:absolute;left:0;right:0;text-align:center;font-size:10.5px;font-weight:500;color:var(--ink)}
.card__title--light{font-size:9px}
.card__text{position:absolute;left:4px;right:4px;text-align:center;font-size:8.3px;line-height:14.2px;color:var(--muted)}
.progress{position:absolute;height:4px;border-radius:2px;background:var(--track)}
.progress__fill{height:100%;border-radius:2px;background:var(--orange-a)}
.stats{position:absolute;left:0;right:0;display:flex;justify-content:center;gap:20px;font-size:11px;font-weight:500}
.stats__item{display:flex;align-items:center;gap:7px}
.stats__item svg{width:13px;height:13px}
.counter{position:absolute;left:37px;display:flex;align-items:center;gap:12px}
.counter__num{font-size:15px;font-weight:600}
.counter__meta{display:flex;flex-direction:column;gap:3px}
.counter__state{font-size:7px;color:var(--soft)}
.counter__label{font-size:8.3px;color:var(--ink)}
.meta{position:absolute;font-size:8.3px;color:var(--muted);transform:translateX(-50%)}
.button{position:absolute;left:647px;top:237px;width:86px;height:23px;border-radius:2px;background:linear-gradient(90deg,var(--orange-a),var(--orange-b));color:var(--white);font-size:8.2px;font-weight:600;display:flex;align-items:center;justify-content:center}
.footer{position:absolute;left:122px;right:0;top:479px;height:39px;background:var(--white);font-size:7.3px;color:var(--ink)}
.footer span{position:absolute;top:16px}
.footer b{font-weight:600}
</style>
</head>
<body>
<svg width="0" height="0" style="position:absolute" aria-hidden="true">
  <defs>
    <linearGradient id="hexFill" x1="0" y1="0" x2="1" y2="1">
      <stop offset="0" stop-color="#f9b64c"/>
      <stop offset="1" stop-color="#ef7a26"/>
    </linearGradient>
    <symbol id="hex" viewBox="0 0 48 52">
      <polygon points="24,3 43,14.5 43,37.5 24,49 5,37.5 5,14.5" fill="url(#hexFill)" stroke="url(#hexFill)" stroke-width="4" stroke-linejoin="round"/>
      <polygon points="24,9.5 37.5,17.5 37.5,34.5 24,42.5 10.5,34.5 10.5,17.5" fill="none" stroke="#fff" stroke-width="2.2" stroke-linejoin="round"/>
    </symbol>
    <symbol id="i-doc" viewBox="0 0 48 52"><path d="M20 20h6l3 3v9h-9z M26 20v3h3" fill="none" stroke="#fff" stroke-width="1.2" stroke-linejoin="round"/></symbol>
    <symbol id="i-pie" viewBox="0 0 48 52"><circle cx="24" cy="27" r="5.5" fill="none" stroke="#fff" stroke-width="1.2"/><path d="M24 21.5v5.5h5.5" fill="none" stroke="#fff" stroke-width="1.2"/></symbol>
    <symbol id="i-bars" viewBox="0 0 48 52"><path d="M18 32h12 M19.5 32v-4 M22.5 32v-6 M25.5 32v-5 M28.5 32v-7 M19 24l3-2 3 2 4-3" fill="none" stroke="#fff" stroke-width="1.1" stroke-linecap="round"/></symbol>
    <symbol id="i-horn" viewBox="0 0 48 52"><path d="M19 25l8-4v10l-8-4z M19 25v2 M21 28l1 4 M29 23l2-1 M29 27l2 1 M28.5 20l1-2" fill="none" stroke="#fff" stroke-width="1.2" stroke-linejoin="round" stroke-linecap="round"/></symbol>
    <symbol id="i-list" viewBox="0 0 48 52"><rect x="18.5" y="20.5" width="11" height="12" rx="1.5" fill="none" stroke="#fff" stroke-width="1.2"/><path d="M21 24h6 M21 27h6 M21 30h4" stroke="#fff" stroke-width="1.1" stroke-linecap="round"/></symbol>
    <symbol id="i-tick" viewBox="0 0 14 14"><circle cx="7" cy="7" r="6" fill="none" stroke="#f39a34" stroke-width="1"/><path d="M4.5 7.2l1.7 1.6 3.3-3.3" fill="none" stroke="#f39a34" stroke-width="1"/></symbol>
    <symbol id="i-file" viewBox="0 0 14 14"><path d="M3 1.5h6l2.5 2.5v8.5H3z M5 5.5h4.5 M5 7.5h4.5 M5 9.5h4.5" fill="none" stroke="#f39a34" stroke-width=".9"/></symbol>
    <symbol id="n-home" viewBox="0 0 12 12"><path d="M1.5 6L6 2l4.5 4 M3 5v5h2.3V7.5h1.4V10H9V5" fill="none" stroke="#fff" stroke-width=".9" stroke-linejoin="round"/></symbol>
    <symbol id="n-bell" viewBox="0 0 12 12"><path d="M3 8.5V5.5a3 3 0 0 1 6 0v3l1 1H2z M5 10.5h2 M1.5 3.5l1-1.5 M10.5 3.5l-1-1.5" fill="none" stroke="#fff" stroke-width=".9" stroke-linejoin="round"/></symbol>
    <symbol id="n-gear" viewBox="0 0 12 12"><circle cx="6" cy="6" r="1.8" fill="none" stroke="#fff" stroke-width=".9"/><circle cx="6" cy="6" r="4.3" fill="none" stroke="#fff" stroke-width=".9" stroke-dasharray="1.6 .9"/></symbol>
    <symbol id="n-sliders" viewBox="0 0 12 12"><path d="M1.5 3h9 M1.5 6h9 M1.5 9h9" stroke="#fff" stroke-width=".8"/><circle cx="4" cy="3" r="1.1" fill="#404040" stroke="#fff" stroke-width=".8"/><circle cx="8" cy="6" r="1.1" fill="#404040" stroke="#fff" stroke-width=".8"/><circle cx="5" cy="9" r="1.1" fill="#404040" stroke="#fff" stroke-width=".8"/></symbol>
    <symbol id="n-page" viewBox="0 0 12 12"><path d="M3 1.5h4l2.5 2.5v6.5H3z" fill="none" stroke="#fff" stroke-width=".9" stroke-linejoin="round"/></symbol>
    <symbol id="t-search" viewBox="0 0 14 14"><circle cx="7" cy="7" r="6.5" fill="#1f3550"/><circle cx="6.6" cy="6.6" r="2.2" fill="none" stroke="#fff" stroke-width="1"/><path d="M8.2 8.2l1.7 1.7" stroke="#fff" stroke-width="1.1"/></symbol>
    <symbol id="t-gear" viewBox="0 0 14 14"><circle cx="7" cy="7" r="2" fill="none" stroke="#f39a34" stroke-width="1"/><circle cx="7" cy="7" r="5" fill="none" stroke="#f39a34" stroke-width="1.3" stroke-dasharray="2 1"/></symbol>
    <symbol id="t-bell" viewBox="0 0 14 14"><path d="M3 10V6.5a4 4 0 0 1 8 0V10l1 1H2z" fill="#e2403a"/><circle cx="7" cy="12.3" r="1.2" fill="#e2403a"/><circle cx="11" cy="3" r="2.3" fill="#2fa84f"/></symbol>
  </defs>
</svg>

<!-- Home screen -->
<section class="screen screen--home">
  <div class="brand"><span class="brand__mark"></span><span class="brand__name">PlumVesta</span></div>
  <header class="topbar">
    <h1 class="topbar__title">Home</h1>
    <svg class="topbar__icon" style="left:508px"><use href="#t-search"/></svg>
    <svg class="topbar__icon" style="left:533px"><use href="#t-gear"/></svg>
    <svg class="topbar__icon" style="left:558px"><use href="#t-bell"/></svg>
    <div class="avatar" role="img" aria-label="User profile photo"><span class="avatar__dot"></span></div>
  </header>
  <nav class="sidebar">
    <div class="nav nav--active" style="top:30px"><svg class="nav__icon"><use href="#n-home"/></svg><span class="nav__label">Home</span></div>
    <div class="nav" style="top:62px"><svg class="nav__icon"><use href="#n-bell"/></svg><span class="nav__label">All Alerts</span></div>
    <div class="nav" style="top:94.5px"><svg class="nav__icon"><use href="#n-gear"/></svg><span class="nav__label">Manage</span></div>
    <div class="nav nav--group" style="top:127px"><span class="nav__label">Campaigns</span><span class="nav__aside">+</span></div>
    <div class="nav" style="top:158.5px"><svg class="nav__icon"><use href="#n-sliders"/></svg><span class="nav__label">Cutom Campaign</span><svg class="nav__chev" viewBox="0 0 6 6"><path d="M1 4l2-2 2 2" fill="none" stroke="#fff" stroke-width=".9"/></svg></div>
    <div class="nav" style="top:179px"><span class="nav__label">Overview</span></div>
    <div class="nav" style="top:199px"><span class="nav__label">File &amp; Honey Tokens</span></div>
    <div class="nav" style="top:219px"><span class="nav__label">Resources</span></div>
    <div class="nav" style="top:238px"><span class="nav__label">Alerts</span></div>
    <div class="nav" style="top:258px"><span class="nav__label">Settings</span></div>
    <div class="nav" style="top:284.5px"><svg class="nav__icon"><use href="#n-page"/></svg><span class="nav__label">Default Campaign</span></div>
  </nav>

  <h2 class="section-title" style="left:134px">Teamspace</h2>
  <h2 class="section-title" style="left:339px">Subscription Overview</h2>
  <h2 class="section-title" style="left:543px">Files &amp; Honey Tokens</h2>

  <article class="card" style="left:135px;top:76px;width:190px;height:141px">
    <svg class="hex" style="top:15px"><use href="#hex"/><use href="#i-doc"/></svg>
    <h3 class="card__title" style="top:71px">Default</h3>
    <p class="card__text" style="top:92px">The Default Client is Created as a<br>part of your user account</p>
  </article>
  <article class="card" style="left:339px;top:76px;width:190px;height:141px">
    <svg class="hex" style="top:15px"><use href="#hex"/><use href="#i-pie"/></svg>
    <h3 class="card__title" style="top:71px">Start Pack Usage</h3>
    <p class="card__text" style="top:92px">0 files active out of 10 allowed</p>
    <div class="progress" style="left:13px;top:117px;width:165px"><div class="progress__fill" style="width:11%"></div></div>
  </article>
  <article class="card" style="left:543px;top:76px;width:190px;height:141px">
    <svg class="hex" style="top:15px"><use href="#hex"/><use href="#i-bars"/></svg>
    <h3 class="card__title" style="top:71px">Statistics</h3>
    <div class="stats" style="top:98px">
      <span class="stats__item"><svg><use href="#i-tick"/></svg>0</span>
      <span class="stats__item"><svg><use href="#i-file"/></svg>30</span>
    </div>
  </article>

  <h2 class="section-title" style="left:134px;top:243px">Campaigns</h2>
  <div class="button">New Campaign</div>

  <article class="card" style="left:135px;top:277px;width:190px;height:170px">
    <svg class="hex" style="top:15px"><use href="#hex"/><use href="#i-horn"/></svg>
    <h3 class="card__title" style="top:71px">My Custom Campaign</h3>
    <p class="card__text" style="top:89px">This is my custom campaign for finding!</p>
    <div class="counter" style="top:116px"><span class="counter__num">0</span><span class="counter__meta"><span class="counter__state">Active</span><span class="counter__label">Files and Honey Tokens</span></span></div>
  </article>
  <article class="card" style="left:339px;top:277px;width:190px;height:170px">
    <svg class="hex" style="top:15px"><use href="#hex"/><use href="#i-list"/></svg>
    <h3 class="card__title" style="top:71px">Default Campaign</h3>
    <p class="card__text" style="top:89px">Define your own mission of combine different</p>
    <div class="counter" style="top:116px"><span class="counter__num">0</span><span class="counter__meta"><span class="counter__state">Active</span><span class="counter__label">Files and Honey Tokens</span></span></div>
  </article>

  <footer class="footer">
    <span style="left:12px"><b>149</b> Nutzer sind online.</span>
    <span style="left:175px">Nordlicht-QX Online. Alle Rechte vorbehalten.</span>
    <span style="right:13px">Produktseite Nordlicht-QX | Widerrufsrecht | Datenschutz | Impressum</span>
  </footer>
</section>

<!-- Campaign overview screen -->
<section class="screen screen--overview">
  <div class="brand"><span class="brand__mark"></span><span class="brand__name">PlumVesta</span></div>
  <header class="topbar">
    <h1 class="topbar__title">Home</h1>
    <svg class="topbar__icon" style="left:508px"><use href="#t-search"/></svg>
    <svg class="topbar__icon" style="left:533px"><use href="#t-gear"/></svg>
    <svg class="topbar__icon" style="left:558px"><use href="#t-bell"/></svg>
    <div class="avatar" role="img" aria-label="User profile photo"><span class="avatar__dot"></span></div>
  </header>
  <nav class="sidebar">
    <div class="nav" style="top:30px"><svg class="nav__icon"><use href="#n-home"/></svg><span class="nav__label">Home</span></div>
    <div class="nav" style="top:62px"><svg class="nav__icon"><use href="#n-bell"/></svg><span class="nav__label">All Alerts</span></div>
    <div class="nav" style="top:94.5px"><svg class="nav__icon"><use href="#n-gear"/></svg><span class="nav__label">Manage</span></div>
    <div class="nav nav--group" style="top:127px"><span class="nav__label">Campaigns</span><span class="nav__aside">+</span></div>
    <div class="nav" style="top:158.5px"><svg class="nav__icon"><use href="#n-sliders"/></svg><span class="nav__label">Cutom Campaign</span><svg class="nav__chev" viewBox="0 0 6 6"><path d="M1 4l2-2 2 2" fill="none" stroke="#fff" stroke-width=".9"/></svg></div>
    <div class="nav nav--active" style="top:181.5px"><span class="nav__label">Overview</span></div>
    <div class="nav" style="top:204px"><span class="nav__label">File &amp; Honey Tokens</span></div>
    <div class="nav" style="top:224px"><span class="nav__label">Resources</span></div>
    <div class="nav" style="top:244px"><span class="nav__label">Alerts</span></div>
    <div class="nav" style="top:263px"><span class="nav__label">Settings</span></div>
    <div class="nav" style="top:284.5px"><svg class="nav__icon"><use href="#n-page"/></svg><span class="nav__label">Default Campaign</span></div>
  </nav>

  <h2 class="section-title" style="left:134px">Campaign</h2>
  <h2 class="section-title" style="left:339px">Campaign Organisation</h2>

  <article class="card" style="left:135px;top:76px;width:190px;height:141px">
    <svg class="hex" style="top:15px"><use href="#hex"/><use href="#i-doc"/></svg>
    <h3 class="card__title card__title--light" style="top:73px">My Cutom Campaign</h3>
    <p class="card__text" style="top:92px">This is my custom campaign for finding</p>
  </article>
  <article class="card" style="left:339px;top:76px;width:394px;height:141px">
    <svg class="hex" style="top:12px;left:96px"><use href="#hex"/><use href="#i-pie"/></svg>
    <h3 class="card__title" style="top:68px;right:auto;left:0;width:192px;line-height:15.8px">Self-enabling Deliverable<br>Proprietary Limited</h3>
    <span class="meta" style="left:98px;top:102px">Standard</span>
    <span class="meta" style="left:170px;top:102px">86 %</span>
    <div class="progress" style="left:15px;top:125px;width:165px"><div class="progress__fill" style="width:86%"></div></div>

    <svg class="hex" style="top:12px;left:294px"><use href="#hex"/><use href="#i-pie"/></svg>
    <h3 class="card__title" style="top:68px;left:192px;right:0">Unleash bleeding-edge mindshare</h3>
    <span class="meta" style="left:295px;top:102px">8 hours ago</span>
    <span class="meta" style="left:368px;top:102px">08%</span>
    <div class="progress" style="left:212px;top:125px;width:165px"><div class="progress__fill" style="width:11%"></div></div>
  </article>

  <h2 class="section-title" style="left:134px;top:243px">Files &amp; Honey Tokens</h2>
  <div class="button">New Campaign</div>

  <article class="card" style="left:135px;top:277px;width:190px;height:138px">
    <svg class="hex" style="top:15px"><use href="#hex"/><use href="#i-bars"/></svg>
    <h3 class="card__title" style="top:72px">Statistics</h3>
    <div class="stats" style="top:99px">
      <span class="stats__item"><svg><use href="#i-tick"/></svg>0</span>
      <span class="stats__item"><svg><use href="#i-file"/></svg>30</span>
    </div>
  </article>
  <article class="card" style="left:339px;top:277px;width:198px;height:138px">
    <svg class="hex" style="top:15px"><use href="#hex"/><use href="#i-list"/></svg>
    <h3 class="card__title" style="top:72px">Resources</h3>
    <p class="card__text" style="top:91px">Genearte a collection of fictional organisations,<br>Custom templates,Upload files and logos</p>
  </article>
  <article class="card" style="left:546px;top:277px;width:187px;height:138px">
    <svg class="hex" style="top:15px"><use href="#hex"/><use href="#i-list"/></svg>
    <h3 class="card__title" style="top:72px">Alerts</h3>
    <p class="card__text" style="top:91px">Alert Statistics will appear here</p>
  </article>

  <footer class="footer">
    <span style="left:12px"><b>149</b> Nutzer sind online.</span>
    <span style="left:175px">Nordlicht-QX Online. Alle Rechte vorbehalten.</span>
    <span style="right:13px">Produktseite Nordlicht-QX | Widerrufsrecht | Datenschutz | Impressum</span>
  </footer>
</section>
</body>
</html>
```